Looking for someone to design a business card for my plumbing business Quandor Plumbing Solutions I want the background also to be black, must attract clients. If possible I want the front to be the logo and the back to show maybe the details.

Target Market(s)

Clients

Industry/Entity Type

Plumbing maintenance

Contact Information for Business Card

Name: Felix, Contact: 0461 539 207, Email: quandorplumbingsolutions@mailbrook.example, Licence number 728093K

Font styles to use
Other font styles liked:
• as per logo maybe?

Colors

Designer to choose colors to be used in the design.

Requirements
Nice to have
• stating the service I provide, emergency plumbing, plumbing maintenance, drainage maintenance, block sewer and stormwater, camera and locating.

```html
<!DOCTYPE html>
<html lang="en">
<head>
<meta charset="utf-8">
<title>Quandor Plumbing Solutions – Business Cards</title>
<link rel="stylesheet" href="https://fonts.googleapis.com/css2?family=Montserrat:wght@400;500;700;800&display=swap">
<style>
  :root {
    --backdrop: #4a4a4a;
    --card: #232324;
    --card-edge: #1a1a1b;
    --blue: #4a8fd6;
    --white: #ffffff;
    --text: #e9e9e9;
    --muted: #d8d8d8;
    --ghost: #2c2c2e;
    --figure: #f2f2f2;
  }
  * { box-sizing: border-box; margin: 0; padding: 0; }
  html, body { width: 1200px; height: 875px; overflow: hidden; }
  body {
    background: var(--backdrop);
    font-family: "Montserrat", sans-serif;
    position: relative;
  }
  .card {
    position: absolute;
    top: 282px;
    width: 560px;
    height: 311px;
    background: var(--card);
    border-radius: 18px;
    box-shadow: 0 14px 30px rgba(0,0,0,.45);
    overflow: hidden;
  }
  .card--front { left: 27px; }
  .card--back { left: 613px; }

  /* front */
  .brand {
    position: absolute;
    display: flex;
    align-items: center;
  }
  .card--front .brand { left: 92px; top: 62px; gap: 18px; }
  .mascot {
    background: var(--figure);
    border-radius: 46% 46% 30% 30%;
    flex: none;
  }
  .card--front .mascot { width: 120px; height: 150px; }
  .brand-name {
    color: var(--blue);
    font-weight: 800;
    text-transform: uppercase;
    line-height: 1.05;
  }
  .card--front .brand-name { font-size: 34px; letter-spacing: .5px; }
  .card--front .brand-name small { display: block; font-size: 19px; letter-spacing: 1px; }
  .services {
    position: absolute;
    left: 0; right: 0; top: 238px;
    text-align: center;
    color: var(--text);
    font-size: 13.5px;
    line-height: 1.6;
    font-weight: 400;
  }
  .dot {
    display: inline-block;
    width: 5px; height: 5px;
    border-radius: 50%;
    background: var(--blue);
    vertical-align: middle;
    margin: 0 7px;
  }

  /* back */
  .ghost-mascot {
    position: absolute;
    right: 40px; top: 24px;
    width: 210px; height: 260px;
    background: var(--ghost);
    border-radius: 46% 46% 30% 30%;
  }
  .card--back .brand { left: 56px; top: 34px; gap: 12px; }
  .card--back .mascot { width: 74px; height: 92px; }
  .card--back .brand-name { font-size: 22px; }
  .card--back .brand-name small { display: block; font-size: 12px; letter-spacing: .6px; }
  .accent-bar {
    position: absolute;
    left: 40px; top: 166px;
    width: 12px; height: 34px;
    background: var(--blue);
  }
  .details {
    position: absolute;
    left: 66px; top: 150px;
    color: var(--text);
    font-size: 12.5px;
    line-height: 1.5;
  }
  .person-name {
    color: var(--blue);
    font-weight: 800;
    font-size: 21px;
    letter-spacing: .5px;
    line-height: 1.1;
  }
  .role { font-weight: 500; }
  .licence { margin-bottom: 8px; }
  .contact { list-style: none; }
  .contact li { display: flex; align-items: center; gap: 8px; }
  .contact svg { width: 12px; height: 12px; flex: none; }
  .contact .social-dot {
    width: 11px; height: 11px; border-radius: 50%;
    background: var(--blue); flex: none;
  }
</style>
</head>
<body>

  <section class="card card--front" aria-label="Business card front">
    <div class="brand">
      <div class="mascot" role="img" aria-label="Mascot illustration: white furry creature holding a pipe wrench"></div>
      <div class="brand-name">Quandor<small>Plumbing Solutions</small></div>
    </div>
    <p class="services">
      Emergency plumbing<span class="dot"></span>Plumbing maintenance<span class="dot"></span>Drainage maintenance<br>
      Block sewer and stormwater<span class="dot"></span>Camera and locating
    </p>
  </section>

  <section class="card card--back" aria-label="Business card back">
    <div class="ghost-mascot" role="img" aria-label="Faint large mascot illustration in the background"></div>
    <div class="brand">
      <div class="mascot" role="img" aria-label="Mascot illustration: white furry creature holding a pipe wrench"></div>
      <div class="brand-name">Quandor<small>Plumbing Solutions</small></div>
    </div>
    <span class="accent-bar"></span>
    <div class="details">
      <p class="person-name">FELIX</p>
      <p class="role">Founder &amp; CEO</p>
      <p class="licence">Licence number 728093K</p>
      <ul class="contact">
        <li>
          <svg viewBox="0 0 24 24" aria-hidden="true"><path fill="var(--blue)" d="M6.6 10.8a15 15 0 0 0 6.6 6.6l2.2-2.2a1 1 0 0 1 1-.25 11.4 11.4 0 0 0 3.6.57 1 1 0 0 1 1 1V20a1 1 0 0 1-1 1A17 17 0 0 1 3 4a1 1 0 0 1 1-1h3.5a1 1 0 0 1 1 1c0 1.25.2 2.45.57 3.6a1 1 0 0 1-.25 1z"/></svg>
          0461 539 207
        </li>
        <li>
          <svg viewBox="0 0 24 24" aria-hidden="true"><rect x="2" y="5" width="20" height="14" rx="1.5" fill="var(--blue)"/><path d="M3 6l9 7 9-7" fill="none" stroke="var(--card)" stroke-width="1.8"/></svg>
          quandorplumbingsolutions@mailbrook.example
        </li>
        <li>
          <span class="social-dot" aria-hidden="true"></span>
          @QuandorPlumbingSolutions
        </li>
      </ul>
    </div>
  </section>

</body>
</html>
```